Business Identity Stationary

Already have the logo which is in the attached files so only need the Business STationary
1) Double Sided Business Card
2) Letterhead
3) Presentation folder with business card holder on inside cover
4) WIth compliments slip
See information for business cards, letterhead and presentation folder below.

This should be a simply job using a logo we already had designed along with a little device. I suggest using the device off center and perhaps lower in the corner in an abstract way. Also the logo device could be used as a watermark for the letterhead. The designer who created the logo presented something that I think works well for a business card. The front of the double sided business card could have the name logo small for the website address and only use the Lime device on the front. Then on the back could be the name Barrow Advisory logo.

Please note that for the business card the black and lime green background do look good. Also please think of using the lime device separately in an unusual way.

It has been brought to my attention that.my budget was far to low. Hopefully this.will attract you to the project. 

The parent company of Barrow Advisory is TallHeron holdings. I have uploaded a file of the Tall Heron business card I really like. Perhaps use this business card as a guide to the type of modern and clean style I am looking for. It also works to have the Barrow Advisroy and Tall Heron similar.

Reason: Still haven't received anything exactly right.

Industry/Entity Type

Business

Font styles to use
Sans Serif

Colors
9bcb3c
000000
5c5c5c
add136
cadf82
eaf2cf
f9fbf2
1b1b1b
757575

Requirements
Must have
• 1) Double Sided Business Card
Marta Kellendorf
Director
Tel: +505 8264 3170
Email: mk@barrowadvisory-example.com
Website: www.barrowadvisory-example.com

Frederick Kellendorf
Director
Tel: +505 8264 3172
Email: fk@barrowadvisory-example.com

Lucia Brenes Otaduy
Director
Tel: 8642 1093
Email: lbo@barrowadvisory-example.com

2) Letterhead
Logo
Lime Logo Device
Website Address: www.barrowadvisory-example.com
Small print on bottom: Barrow Advisory a Tall Heron Holding Company SA. RUC J0487000239518

3) Presentation Folder
Traditional Presentation folder with inside front cover spot for the insertion of business card.

4) With Compliments slip

```html
<!DOCTYPE html>
<html lang="en">
<head>
<meta charset="utf-8">
<title>Barrow Advisory – Business Card</title>
<link href="https://fonts.googleapis.com/css2?family=Questrial&display=swap" rel="stylesheet">
<style>
  :root {
    --lime: #9bcb3c;
    --black: #000000;
    --ink: #1b1b1b;
    --grey: #5c5c5c;
    --grey-light: #757575;
    --grey-soft: #9a9a9a;
    --paper: #ffffff;
    --backdrop: #ececec;
  }
  * { margin: 0; padding: 0; box-sizing: border-box; }
  html, body {
    width: 1200px; height: 1000px; overflow: hidden;
    background: radial-gradient(ellipse at 50% 40%, #fafafa 0%, var(--backdrop) 70%, #dedede 100%);
    font-family: "Questrial", "Century Gothic", sans-serif;
  }
  .stage { position: relative; width: 1200px; height: 1000px; }

  .card {
    position: absolute; width: 725px; height: 360px; border-radius: 40px;
  }
  .card--front { left: 140px; top: 85px; background: var(--black); }
  .card--back  { left: 335px; top: 500px; background: var(--paper); }

  /* front */
  .front-wordmark {
    position: absolute; left: 0; right: 0; top: 150px;
    display: flex; justify-content: center; align-items: center; gap: 18px;
  }
  .front-wordmark__name {
    color: var(--paper); font-size: 56px; letter-spacing: 1px; line-height: 1;
  }
  .front-wordmark__dot {
    width: 36px; height: 36px; border-radius: 50%; background: var(--lime);
  }

  /* back */
  .back-wordmark {
    position: absolute; left: 58px; top: 42px;
    display: flex; align-items: center; gap: 10px;
  }
  .back-wordmark__name { color: var(--ink); font-size: 27px; line-height: 1; }
  .back-wordmark__dot { width: 16px; height: 16px; border-radius: 50%; background: var(--lime); }

  .holder { position: absolute; left: 58px; top: 143px; }
  .holder__name { color: var(--grey); font-size: 27px; letter-spacing: 2px; line-height: 1.1; }
  .holder__role { color: var(--grey-soft); font-size: 16px; letter-spacing: 1px; margin-top: 2px; }

  .contact { position: absolute; left: 345px; top: 152px; list-style: none; }
  .contact__item {
    display: flex; align-items: center; gap: 5px;
    color: var(--grey); font-size: 19px; letter-spacing: 1px; line-height: 28px;
  }
  .contact__icon { width: 18px; height: 18px; flex: none; }

  .legal {
    position: absolute; left: 0; right: 0; top: 252px; text-align: center;
    color: var(--grey); font-size: 15px; letter-spacing: 1.6px; line-height: 24px;
  }
  .website {
    position: absolute; left: 0; right: 0; top: 306px; text-align: center;
    color: var(--grey); font-size: 19px; font-weight: 700; letter-spacing: 1.5px;
  }
</style>
</head>
<body>
<main class="stage">
  <section class="card card--front" aria-label="Business card front">
    <div class="front-wordmark">
      <span class="front-wordmark__name">Barrow Advisory</span>
      <span class="front-wordmark__dot"></span>
    </div>
  </section>

  <section class="card card--back" aria-label="Business card back">
    <div class="back-wordmark">
      <span class="back-wordmark__name">Barrow Advisory</span>
      <span class="back-wordmark__dot"></span>
    </div>

    <div class="holder">
      <p class="holder__name">Marta Kellendorf</p>
      <p class="holder__role">Director</p>
    </div>

    <ul class="contact">
      <li class="contact__item">
        <svg class="contact__icon" viewBox="0 0 18 18" aria-hidden="true">
          <rect x="4.5" y="1" width="9" height="16" rx="1.5" fill="none" stroke="var(--lime)" stroke-width="1.6"/>
          <line x1="7.5" y1="14.5" x2="10.5" y2="14.5" stroke="var(--lime)" stroke-width="1.4"/>
        </svg>
        +505 8264 3170
      </li>
      <li class="contact__item">
        <svg class="contact__icon" viewBox="0 0 18 18" aria-hidden="true">
          <rect x="1" y="4" width="16" height="11" rx="1" fill="var(--lime)"/>
          <polyline points="1.5,4.5 9,10.5 16.5,4.5" fill="none" stroke="var(--paper)" stroke-width="1.2"/>
        </svg>
        mk@barrowadvisory-example.com
      </li>
    </ul>

    <div class="legal">
      <p>Barrow Advisory a Tall Heron Holding Company SA.</p>
      <p>RUC J0487000239518</p>
    </div>
    <p class="website">www.barrowadvisory-example.com</p>
  </section>
</main>
</body>
</html>
```